Resposive web site in 4 languages + image gallery + logo design

We need a web page, which will work on all devices.
I have uploaded web page concept.
Company name: Praxelun
Industry/Entity Type
It Company
Logo Text
quality matters
Coding
Coded - Design and coding required
Number of Pages Required
1 page

```html
<!DOCTYPE html>
<html lang="en">
<head>
<meta charset="utf-8">
<title>Praxelun</title>
<link rel="stylesheet" href="https://fonts.googleapis.com/css2?family=Lato:wght@400;700&family=Questrial&display=swap">
<style>
:root{
  --ink:#2b2b2b;
  --muted:#555;
  --white:#fff;
  --wood:#3b2416;
  --wood-dark:#24150c;
  --charcoal:#3a3a3a;
  --charcoal-dark:#2c2c2c;
  --footer:#313131;
  --bar:#1e1e1e;
  --like:#4a6fb5;
}
*{margin:0;padding:0;box-sizing:border-box}
html,body{width:1200px;height:2329px;overflow:hidden}
body{position:relative;font-family:'Lato',sans-serif;color:var(--ink);background:var(--white)}
h1,h2,h3{font-weight:400}
.abs{position:absolute}
.heading{font-family:'Questrial',sans-serif;font-weight:400}
/* header */
.site-header{left:0;top:0;width:1200px;height:85px;background:var(--white);border-top:2px solid #ddd}
.brand{left:132px;top:28px;font-size:30px;letter-spacing:1px;color:#222}
.nav{top:45px;font-size:16px;color:#222}
.nav-active{border-bottom:2px solid #222;padding-bottom:4px}
.lang-flag{left:905px;top:43px;width:43px;height:22px;background:linear-gradient(135deg,#27367a,#c8102e 50%,#27367a)}
.like-btn{left:997px;top:39px;width:71px;height:29px;background:var(--like);border:1px solid #2f4f8f;border-radius:3px;color:#fff;font-weight:700;font-size:15px;text-align:center;line-height:27px}
/* hero */
.hero{left:0;top:85px;width:1200px;height:499px;background:radial-gradient(ellipse at 50% 55%,#8a5a32,#5a3a22 55%,#2e1e14)}
.hero-arrow{top:315px;width:43px;height:40px;background:#2a2a2a;border:1px solid #777;display:flex;align-items:center;justify-content:center}
.hero-title{left:0;top:312px;width:1200px;text-align:center;font-weight:700;font-size:37px;color:#fff;text-shadow:0 2px 4px rgba(0,0,0,.6)}
.quote-btn{left:506px;top:376px;width:188px;height:49px;border:2px solid #fff;color:#fff;font-weight:700;font-size:18px;text-align:center;line-height:45px}
/* section titles */
.sec-title{left:0;width:1200px;text-align:center;font-size:31px}
.divider{left:283px;width:634px;height:12px}
/* welcome */
.intro{left:160px;top:707px;width:880px;text-align:center;font-size:15.5px;line-height:25.5px;color:#222}
.outline-btn{border:1.5px solid #222;text-align:center;font-weight:700;color:#222}
/* services */
.services{left:0;top:913px;width:1200px;height:472px;background:linear-gradient(90deg,var(--wood-dark),var(--wood) 30%,#4a2d1a 50%,var(--wood) 70%,var(--wood-dark))}
.card-photo{top:1039px;width:296px;height:180px;border:7px solid #fff}
.card-title{top:1240px;width:296px;text-align:center;font-weight:700;font-size:22px;letter-spacing:1px;color:#fff}
.card-text{top:1282px;width:264px;text-align:center;font-size:15px;line-height:20.5px;color:#f2f2f2}
/* gallery */
.filter{top:1502px;font-size:15px;color:#333;display:flex;align-items:center;gap:9px}
.box{width:17px;height:17px;border:1.5px solid #555;background:#fff}
.thumb{top:1549px;width:219px;height:143px;border:2px solid #bbb;padding:5px;background:#fff}
.thumb-fill{width:100%;height:100%}
.thumb-caption{left:7px;top:7px;right:7px;bottom:7px;background:rgba(40,40,40,.75);color:#fff;text-align:center}
/* contact */
.contact{left:0;top:1742px;width:1200px;height:340px;background:linear-gradient(180deg,var(--charcoal),var(--charcoal-dark))}
.col-head{top:1777px;font-family:'Questrial',sans-serif;font-size:20px;color:#fff}
.col-rule{top:1813px;height:1px;border-top:1px dashed #888}
.field{background:#fff;font-size:12.5px;color:#444;padding:6px 8px}
.submit{left:132px;top:2015px;width:84px;height:31px;border:1.5px solid #ddd;color:#fff;font-weight:700;font-size:13px;text-align:center;line-height:28px}
.testimonial{left:629px;top:1832px;width:439px;height:151px;background:#fff;border-radius:8px;padding:14px 18px 0 58px;font-size:13px;font-style:italic;line-height:22px;color:#333}
.avatar{left:655px;top:1970px;width:74px;height:74px;border-radius:50%;border:3px solid #fff;background:linear-gradient(#c9a48a,#8a6a55)}
/* footer */
.footer{left:0;top:2082px;width:1200px;height:209px;background:var(--footer)}
.foot-head{top:2119px;font-size:18px;color:#fff}
.foot-rule{top:2147px;height:1px;border-top:1px dashed #666}
.foot-link{left:132px;font-size:13px;color:#eee}
.foot-text{font-size:13px;color:#eee;line-height:18px}
.vsep{top:2120px;width:1px;height:140px;background:#444}
.copyright{left:0;top:2291px;width:1200px;height:38px;background:var(--bar);color:#ddd;font-size:12px;text-align:center;line-height:38px}
</style>
</head>
<body>

<header class="abs site-header">
  <div class="abs brand">PRAXELUN</div>
  <nav>
    <span class="abs nav nav-active" style="left:470px">HOME</span>
    <span class="abs nav" style="left:553px">SERVICES</span>
    <span class="abs nav" style="left:658px">ABOUT US</span>
    <span class="abs nav" style="left:772px">CONTACT US</span>
  </nav>
  <div class="abs lang-flag" role="img" aria-label="English language flag"></div>
  <svg class="abs" style="left:958px;top:50px" width="12" height="8"><path d="M0 0h12L6 7z" fill="#222"/></svg>
  <div class="abs like-btn">Like</div>
</header>

<section class="abs hero" role="img" aria-label="Photo of a wooden kitchen with granite countertops"></section>
<div class="abs hero-arrow" style="left:5px"><svg width="12" height="16"><path d="M10 2L3 8l7 6" stroke="#fff" stroke-width="3" fill="none"/></svg></div>
<div class="abs hero-arrow" style="left:1152px"><svg width="12" height="16"><path d="M2 2l7 6-7 6" stroke="#fff" stroke-width="3" fill="none"/></svg></div>
<h1 class="abs hero-title">Are you interested in an estimate?</h1>
<div class="abs quote-btn">GET A QUOTE</div>

<h2 class="abs heading sec-title" style="top:622px">Welcome to PRAXELUN</h2>
<svg class="abs divider" style="top:677px" viewBox="0 0 634 12"><line x1="0" y1="6" x2="634" y2="6" stroke="#444"/><circle cx="317" cy="6" r="5" fill="#222"/></svg>
<p class="abs intro">Praxelun is a company whose business operations include making wooden products, restoration and building structures from natural stone. All of our products are made by craftsmen and specialists who have extensive experience and knowledge in their fields. The products we offer are always handmade and we take the requests and ideas of the specific client into account We always strive to achieve the best possible quality.</p>
<div class="abs outline-btn" style="left:532px;top:829px;width:134px;height:36px;line-height:33px;font-size:15px">READ MORE</div>

<section class="abs services" role="img" aria-label="Dark wood plank background"></section>
<h2 class="abs heading sec-title" style="top:948px;color:#fff">Featured Services</h2>
<svg class="abs divider" style="top:1003px" viewBox="0 0 634 12"><line x1="0" y1="6" x2="634" y2="6" stroke="#bbb"/><circle cx="317" cy="6" r="5" fill="#fff"/></svg>

<div class="abs card-photo" style="left:132px;background:linear-gradient(135deg,#d8cbb8,#9a5a2c 60%,#5a3020)" role="img" aria-label="Wooden staircase in a living room"></div>
<div class="abs card-photo" style="left:452px;background:linear-gradient(135deg,#e8e8e6,#b9b2a6 55%,#7a6a58)" role="img" aria-label="Kitchen with stone column and counter"></div>
<div class="abs card-photo" style="left:772px;background:linear-gradient(90deg,#b96a3c,#9c5632 70%,#6f8f4f)" role="img" aria-label="Workers restoring a wooden house wall"></div>

<h3 class="abs card-title" style="left:132px">WOODWORKS</h3>
<h3 class="abs card-title" style="left:452px">STONE WORKS</h3>
<h3 class="abs card-title" style="left:772px">RESTORATION</h3>
<p class="abs card-text" style="left:148px">Timber is, in essence, a natural and warm material. Wood is also relatively durable and easy to work with... [+]</p>
<p class="abs card-text" style="left:468px">The natural stone found in the ground has been used in construction for centuries because of its durability... [+]</p>
<p class="abs card-text" style="left:788px">It's good to see that fixing old things has become popular again in recent years and people... [+]</p>

<h2 class="abs heading sec-title" style="top:1423px">Projects Gallery</h2>
<svg class="abs divider" style="top:1472px" viewBox="0 0 634 12"><line x1="0" y1="6" x2="634" y2="6" stroke="#444"/><circle cx="317" cy="6" r="5" fill="#222"/></svg>
<div class="abs filter" style="left:345px"><span class="box" style="position:relative"><svg class="abs" style="left:1px;top:0" width="14" height="14"><path d="M2 7l4 4 7-9" stroke="#222" stroke-width="2" fill="none"/></svg></span>All</div>
<div class="abs filter" style="left:447px"><span class="box"></span>Woodworks</div>
<div class="abs filter" style="left:603px"><span class="box"></span>Stone Works</div>
<div class="abs filter" style="left:749px"><span class="box"></span>Restoration</div>

<svg class="abs" style="left:88px;top:1608px" width="16" height="26"><path d="M13 2L3 13l10 11" stroke="#111" stroke-width="2.5" fill="none"/></svg>
<svg class="abs" style="left:1096px;top:1608px" width="16" height="26"><path d="M3 2l10 11L3 24" stroke="#111" stroke-width="2.5" fill="none"/></svg>

<div class="abs thumb" style="left:132px"><div class="thumb-fill" style="background:linear-gradient(160deg,#3a3450,#5a4a40 60%,#2a2420)" role="img" aria-label="Living room interior at night"></div></div>
<div class="abs thumb" style="left:371px;box-shadow:0 3px 8px rgba(0,0,0,.4)">
  <div class="thumb-fill" style="background:linear-gradient(160deg,#6a7280,#40464f)" role="img" aria-label="Workshop interior"></div>
  <div class="abs thumb-caption">
    <div style="margin-top:38px;font-weight:700;font-size:15px">Lorem ipsum dolor</div>
    <div style="margin-top:6px;font-size:13px;line-height:19px">Lorem ipsum dolor sit amet consectetur adipiscing elit.</div>
  </div>
</div>
<div class="abs thumb" style="left:610px"><div class="thumb-fill" style="background:linear-gradient(160deg,#4a3a30,#2a1e18 60%,#6a5040)" role="img" aria-label="Dark wooden kitchen with pendant lights"></div></div>
<div class="abs thumb" style="left:849px"><div class="thumb-fill" style="background:linear-gradient(160deg,#2a2850,#6a4a6a 55%,#c89070)" role="img" aria-label="Chandelier in a stairwell"></div></div>

<section class="abs contact" role="img" aria-label="Dark textured background"></section>
<h2 class="abs col-head" style="left:132px">GET IN TOUCH WITH US</h2>
<div class="abs col-rule" style="left:132px;width:436px"></div>
<p class="abs" style="left:132px;top:1826px;font-size:13px;color:#fff">Lorem ipsum dolor sit amet consectetuer adipiscing sed dmmy nibh</p>
<div class="abs field" style="left:132px;top:1860px;width:206px;height:28px">First Name</div>
<div class="abs field" style="left:359px;top:1860px;width:209px;height:28px">Last Name</div>
<div class="abs field" style="left:132px;top:1899px;width:206px;height:28px">Email</div>
<div class="abs field" style="left:359px;top:1899px;width:209px;height:28px">Phone</div>
<div class="abs field" style="left:132px;top:1934px;width:436px;height:67px">Your Message</div>
<div class="abs submit">SUBMIT</div>

<h2 class="abs col-head" style="left:629px">CLIENT TESTIMONIALS</h2>
<svg class="abs" style="left:1037px;top:1780px" width="34" height="16"><path d="M9 2L3 8l6 6M25 2l6 6-6 6" stroke="#ccc" stroke-width="1.8" fill="none"/></svg>
<div class="abs col-rule" style="left:629px;width:439px"></div>
<div class="abs testimonial">Lorem ipsum dolor sit amet consetug e sed diay nibh euismodl tincidunt ut laoreet dolore magam er vol wisi enim ad minim veniam quis nostrud exerci tationorem ipsum dolor sit ametee sed diammmy nibh euismod tincidunt ut laoreet dolore magna aliqur volpatl tiidunt ut laoreet dolore magna aliqur volpatl</div>
<svg class="abs" style="left:652px;top:1844px" width="34" height="26"><path d="M4 24l7-20h7L12 24zM18 24l7-20h7l-6 20z" fill="#ccc"/></svg>
<svg class="abs" style="left:960px;top:1980px" width="60" height="36"><path d="M0 0h60L10 34z" fill="#fff"/></svg>
<div class="abs avatar" role="img" aria-label="Client portrait"></div>
<div class="abs" style="left:748px;top:2007px;font-weight:700;font-size:14px;color:#fff">Mr. Alden Marrow</div>

<footer class="abs footer"></footer>
<div class="abs vsep" style="left:295px"></div>
<div class="abs vsep" style="left:570px"></div>
<div class="abs vsep" style="left:835px"></div>
<h3 class="abs foot-head" style="left:132px">Quick Links</h3>
<div class="abs foot-rule" style="left:132px;width:105px"></div>
<div class="abs foot-link" style="top:2157px">›&nbsp;&nbsp; Home</div>
<div class="abs foot-link" style="top:2183px">›&nbsp;&nbsp; Services</div>
<div class="abs foot-link" style="top:2209px">›&nbsp;&nbsp; About Us</div>
<div class="abs foot-link" style="top:2236px">›&nbsp;&nbsp; Contact Us</div>

<h3 class="abs foot-head" style="left:345px">Contact Information</h3>
<div class="abs foot-rule" style="left:345px;width:170px"></div>
<svg class="abs" style="left:346px;top:2158px" width="12" height="17"><path d="M6 16C1 9 1 7 1 6a5 5 0 0110 0c0 1 0 3-5 10z" fill="#eee"/><circle cx="6" cy="6" r="2" fill="#313131"/></svg>
<div class="abs foot-text" style="left:372px;top:2155px">Veski 12 10115 Norvald<br>ESTLAND</div>
<svg class="abs" style="left:346px;top:2199px" width="14" height="14"><path d="M3 1l3 3-2 2c1 2 2 3 4 4l2-2 3 3-2 2C6 13 1 8 1 3z" fill="#eee"/></svg>
<div class="abs foot-text" style="left:372px;top:2197px">014-552-7310</div>
<svg class="abs" style="left:346px;top:2235px" width="14" height="10"><rect width="14" height="10" fill="#eee"/><path d="M0 0l7 6 7-6" stroke="#313131" fill="none"/></svg>
<div class="abs foot-text" style="left:372px;top:2231px">sales@praxelun.com</div>

<h3 class="abs foot-head" style="left:612px">Location Map</h3>
<div class="abs foot-rule" style="left:612px;width:176px"></div>
<div class="abs" style="left:612px;top:2159px;width:174px;height:89px;border:2px solid #fff;background:linear-gradient(135deg,#cfe0f0,#e8e2c8 50%,#a8c8e8)" role="img" aria-label="Location map"></div>

<div class="abs" style="left:880px;top:2180px;font-size:30px;color:#777;letter-spacing:1px">PRAXELUN</div>

<div class="abs copyright">Copyright © 2016 PRAXELUN. All Rights Reserved.</div>
</body>
</html>
```